Tallowbrook Business Card Design

Design new, 2 sides, business cards for a residential and light commercial heating, air conditioning contractor.

Target Market(s)

Homeowners, small businesses

Industry/Entity Type

Business

Contact Information for Business Card

Dominic Westerhall
Phone - 862-415-2736
Email
Address - PO box 518
Brightwater NJ 07912
Website - www.HarborBreezeLLC.example

Requirements
Must have
• logo, company colors, standard size with no die cut, so I can use nova stamp

```html
<!DOCTYPE html>
<html lang="en">
<head>
<meta charset="utf-8">
<title>Tallowbrook Business Card</title>
<link rel="stylesheet" href="https://fonts.googleapis.com/css2?family=Open+Sans:wght@400;600;700&display=swap">
<style>
  :root {
    --crimson: #9c1c33;
    --orange: #f39c1f;
    --cream: #fbe3b0;
    --ink: #555a60;
    --paper: #ffffff;
    --backdrop: #9a9a9a;
  }
  * { box-sizing: border-box; margin: 0; padding: 0; }
  html, body { width: 1200px; height: 950px; overflow: hidden; }
  body {
    background: var(--backdrop);
    font-family: "Open Sans", Arial, sans-serif;
    position: relative;
  }
  .card {
    position: absolute;
    width: 720px;
    height: 411px;
    box-shadow: 0 10px 24px rgba(0,0,0,0.35);
    overflow: hidden;
  }
  /* Front side */
  .card-front {
    left: 170px; top: 44px;
    background: var(--crimson);
    display: flex; flex-direction: column; align-items: center; justify-content: center;
    color: var(--paper);
  }
  .front-brand {
    display: flex; align-items: center; gap: 16px;
    margin-bottom: 34px;
  }
  .brand-dot {
    width: 30px; height: 30px; border-radius: 50%;
    background: var(--orange);
    flex: none;
  }
  .front-brand .brand-name {
    font-size: 54px; font-weight: 700; letter-spacing: 1px;
    color: var(--cream); text-transform: uppercase; white-space: nowrap;
  }
  .tagline {
    text-align: center; font-size: 20px; line-height: 1.4; font-weight: 400;
  }
  /* Back side */
  .card-back {
    left: 310px; top: 495px;
    background: var(--paper);
    color: var(--ink);
  }
  .side-tab {
    position: absolute; left: 0; top: 84px;
    width: 12px; height: 40px; background: var(--orange);
  }
  .person { position: absolute; left: 44px; top: 70px; }
  .person-name {
    font-size: 26px; font-weight: 600; color: var(--crimson);
    text-transform: uppercase; letter-spacing: 0.5px; white-space: nowrap;
  }
  .person-title { font-size: 18px; color: var(--orange); margin-top: 2px; }
  .address {
    position: absolute; left: 44px; top: 172px;
    font-size: 17px; line-height: 1.35;
  }
  .contact-list {
    position: absolute; left: 44px; top: 234px;
    list-style: none; font-size: 17px; line-height: 1.4;
  }
  .contact-list li { display: flex; align-items: center; gap: 10px; white-space: nowrap; }
  .contact-list svg { width: 15px; height: 15px; fill: var(--crimson); flex: none; }
  .back-brand {
    position: absolute; right: 44px; top: 128px;
    display: flex; align-items: center; gap: 12px;
  }
  .back-brand .brand-dot { width: 24px; height: 24px; }
  .back-brand .brand-name {
    font-size: 36px; font-weight: 700; color: var(--crimson);
    text-transform: uppercase; white-space: nowrap;
  }
  .band-crimson {
    position: absolute; left: 0; bottom: 0;
    width: 100%; height: 34px; background: var(--crimson);
  }
  .band-orange {
    position: absolute; right: 0; bottom: 34px;
    width: 170px; height: 16px; background: var(--orange);
  }
</style>
</head>
<body>

  <section class="card card-front" aria-label="Card front">
    <div class="front-brand">
      <span class="brand-dot"></span>
      <span class="brand-name">Tallowbrook</span>
    </div>
    <p class="tagline">Residential &amp; light commercial heating<br>Air conditioning contractor</p>
  </section>

  <section class="card card-back" aria-label="Card back">
    <span class="side-tab"></span>
    <div class="person">
      <h1 class="person-name">Dominic Westerhall</h1>
      <p class="person-title">CEO/Founder</p>
    </div>
    <p class="address">PO box 518<br>Brightwater NJ 07912</p>
    <ul class="contact-list">
      <li>
        <svg viewBox="0 0 16 16"><path d="M3.5 1.5l2.5 0 1 3.5-1.7 1.2c.8 1.7 2.1 3 3.8 3.8L10.3 8.3l3.5 1v2.5c0 .9-.8 1.7-1.7 1.6C6.8 13 2.9 9.1 1.9 3.2 1.8 2.3 2.6 1.5 3.5 1.5z"/></svg>
        862-415-2736
      </li>
      <li>
        <svg viewBox="0 0 16 16"><path d="M4.5 1h7c.6 0 1 .4 1 1v12c0 .6-.4 1-1 1h-7c-.6 0-1-.4-1-1V2c0-.6.4-1 1-1zm1 2v8h5V3h-5zm2.5 9.2a.9.9 0 100 1.8.9.9 0 000-1.8z"/></svg>
        862-415-2791
      </li>
      <li>
        <svg viewBox="0 0 16 16"><path d="M4 1h8v4H4zM2 6h12c.6 0 1 .4 1 1v5h-3v3H4v-3H1V7c0-.6.4-1 1-1zm3 5v3h6v-3z"/></svg>
        862-415-2744
      </li>
      <li>
        <svg viewBox="0 0 16 16"><path d="M1 3h14v10H1zm1.5 1.2v.4L8 8.5l5.5-3.9v-.4z"/></svg>
        dominic@tallowbrookllc.example
      </li>
      <li>
        <svg viewBox="0 0 16 16"><path d="M8 1a7 7 0 100 14A7 7 0 008 1zm0 1.5c.8 0 1.8 1.6 2 4.5H6c.2-2.9 1.2-4.5 2-4.5zM6 9h4c-.2 2.9-1.2 4.5-2 4.5S6.2 11.9 6 9z"/></svg>
        www.TallowbrookLLC.example
      </li>
    </ul>
    <div class="back-brand">
      <span class="brand-dot"></span>
      <span class="brand-name">Tallowbrook</span>
    </div>
    <span class="band-orange"></span>
    <span class="band-crimson"></span>
  </section>

</body>
</html>
```